Corporate Business Card

Very professional, Modern, Not to busy, include phone address email, website
(253) 617-4930, 18761 52nd Avenue S, Kent, WA 98047, martin@plumlinegroup.com, varkoworks.com

Target Market(s)

Manufacturing

Industry/Entity Type

Aero, machining, manufacturing, Off road racing

Contact Information for Business Card

Phone, address email, website

```html
<!DOCTYPE html>
<html lang="en">
<head>
<meta charset="utf-8">
<title>Varko Works – Business Card</title>
<link href="https://fonts.googleapis.com/css2?family=Exo+2:wght@700&family=Roboto:wght@400;700&display=swap" rel="stylesheet">
<style>
  :root {
    --backdrop: #2b2b2b;
    --navy: #283768;
    --navy-ink: #26335f;
    --red: #c0262b;
    --paper: #ededed;
    --white: #f2f2f2;
  }
  * { margin: 0; padding: 0; box-sizing: border-box; }
  html, body { width: 1200px; height: 1138px; overflow: hidden; }
  body { background: var(--backdrop); position: relative; font-family: "Roboto", sans-serif; }

  .card { position: absolute; border-radius: 16px; overflow: hidden; }

  .card-front { left: 274px; top: 186px; width: 623px; height: 376px; background: var(--navy); }
  .card-front .brand-name {
    position: absolute; left: 0; right: 0; top: 130px; text-align: center;
    font-family: "Roboto", sans-serif; font-weight: 700; font-size: 58px;
    letter-spacing: 2px; color: var(--white);
  }
  .card-front .web-line {
    position: absolute; left: 0; right: 0; top: 327px; text-align: center;
    font-size: 17px; letter-spacing: 13px; color: var(--white);
  }
  .card-front .web-line .accent { color: var(--red); }

  .card-back { left: 276px; top: 608px; width: 618px; height: 374px; background: var(--paper); }
  .person-name {
    position: absolute; left: 36px; top: 44px;
    font-family: "Exo 2", sans-serif; font-weight: 700; font-size: 27px; letter-spacing: 0.5px;
    color: var(--navy-ink);
  }
  .person-name .surname { color: var(--red); }

  .contact-list { position: absolute; left: 35px; top: 186px; list-style: none; }
  .contact-list li {
    display: flex; align-items: flex-start; gap: 10px;
    font-size: 17px; line-height: 24.4px; color: var(--navy-ink);
  }
  .contact-list svg { width: 16px; height: 16px; margin-top: 4px; flex: none; fill: var(--red); }

  .divider { position: absolute; left: 36px; top: 321px; width: 422px; height: 2px; background: var(--navy-ink); }
  .card-back .brand-name {
    position: absolute; right: 40px; top: 278px;
    font-family: "Roboto", sans-serif; font-weight: 700; font-size: 34px; letter-spacing: 1px;
    color: var(--navy-ink);
  }
</style>
</head>
<body>
  <section class="card card-front">
    <div class="brand-name">VARKO WORKS</div>
    <div class="web-line">www.varko<span class="accent">works</span>.com</div>
  </section>

  <section class="card card-back">
    <h1 class="person-name">MARTIN <span class="surname">HALE</span></h1>
    <ul class="contact-list">
      <li>
        <svg viewBox="0 0 16 16"><path d="M8 0a6 6 0 0 0-6 6c0 4.5 6 10 6 10s6-5.5 6-10a6 6 0 0 0-6-6zm0 8.5A2.5 2.5 0 1 1 8 3.5a2.5 2.5 0 0 1 0 5z"/></svg>
        <span>18761 52nd Avenue S,<br>Kent, WA 98047</span>
      </li>
      <li>
        <svg viewBox="0 0 16 16"><path d="M1 5c0-2 3-3 7-3s7 1 7 3v1h-4V4.5H5V6H1zM4 7h8l2 7H2z"/></svg>
        <span>(253) 617-4930</span>
      </li>
      <li>
        <svg viewBox="0 0 16 16"><path d="M1 3h14v1.5L8 9 1 4.5zM1 6.3l7 4.5 7-4.5V13H1z"/></svg>
        <span>martin@plumlinegroup.com</span>
      </li>
      <li>
        <svg viewBox="0 0 16 16"><path d="M8 1a7 7 0 1 0 0 14A7 7 0 0 0 8 1zm0 1.5c.9 0 1.8 1.9 2 4.7H6c.2-2.8 1.1-4.7 2-4.7zM2.6 7.2a5.5 5.5 0 0 1 2.3-3.9c-.3 1-.5 2.4-.6 3.9zm0 1.6h1.7c.1 1.5.3 2.9.6 3.9a5.5 5.5 0 0 1-2.3-3.9zM8 13.5c-.9 0-1.8-1.9-2-4.7h4c-.2 2.8-1.1 4.7-2 4.7zm3.1-.8c.3-1 .5-2.4.6-3.9h1.7a5.5 5.5 0 0 1-2.3 3.9zm.6-5.5c-.1-1.5-.3-2.9-.6-3.9a5.5 5.5 0 0 1 2.3 3.9z"/></svg>
        <span>www.varkoworks.com</span>
      </li>
    </ul>
    <div class="divider"></div>
    <div class="brand-name">VARKO WORKS</div>
  </section>
</body>
</html>
```